Zvo Klinieken website for a maxillofacial surgery clinic

It's a website for a clinic for maxillofacial surgery in WordPress . The website doesn't need to be complicated but has to look professional. It needs to be in Dutch so i can give the texts. Similar websites are www.tandartsenpraktijkveldorm.nl or www.pbtspecialisten.nl. Pages would be sort of similar to https://hetcentrumvoorgezichtszorg.nl/ or https://wervelmondclinics.nl/. Those lasts are maxillofacial surgery clinic websites, but there are little more extensive.
I uploaded the logo. If this is not the proper quality i can upload the eps. Logo was made through pixelforum.

Target Market(s)

Patients who can find me and see information about the clinic

Industry/Entity Type

Healthcare

Coding

Coded - Design and coding required

Number of Pages Required

5+ page

Font styles to use
Other font styles liked:
• Something standard professional

Colors
0054AA
0677BA
7BADD7
CADEEF
E8F1F8

Requirements
Nice to have
• Something in line with the logo. I prefer a little dark like the darker logos but I'm not sure if that's professional. Logos bkvzo and rlpw are instances i'm registered to so they will have to be on the website too but small somewhere.

```html
<!DOCTYPE html>
<html lang="nl">
<head>
<meta charset="utf-8">
<title>Zvo Klinieken</title>
<link href="https://fonts.googleapis.com/css2?family=Open+Sans:wght@400;600;700&family=Rubik:wght@400;500;600&display=swap" rel="stylesheet">
<style>
:root{
  --navy:#1b2d4a;
  --navy-deep:#0f2a48;
  --navy-card:#1f3c5e;
  --blue:#1b9ee0;
  --blue-dark:#0054aa;
  --ink:#27374f;
  --muted:#6f7a88;
  --soft:#f2f4f7;
  --line:#dde3ea;
  --white:#ffffff;
}
*{margin:0;padding:0;box-sizing:border-box}
html,body{width:1200px;height:4841px;overflow:hidden}
body{position:relative;background:var(--white);font-family:"Open Sans",Arial,sans-serif;color:var(--ink)}
.abs{position:absolute}
h1,h2,h3,.heading{font-family:"Rubik",Arial,sans-serif;font-weight:500}
.photo{position:absolute}
.btn{position:absolute;display:flex;align-items:center;justify-content:center;gap:10px;background:var(--blue);color:#fff;font-size:15px;font-weight:700;border-radius:2px}
.kicker{position:absolute;font-size:12px;color:var(--blue-dark);text-transform:uppercase;text-decoration:underline}

/* top bar */
.topbar{left:0;top:0;width:1200px;height:47px;background:var(--navy);color:#dfe6ef;font-size:14px}
.topbar span{position:absolute;top:15px}
/* header */
.logo{display:flex;align-items:center;gap:10px;font-family:"Rubik",sans-serif;font-weight:500;color:#2f8fd0}
.logo i{display:block;border-radius:50%;border:3px solid #2f8fd0}
.contact-item{font-size:13px;line-height:21px;color:var(--ink)}
.contact-item small{color:var(--muted);font-size:13px}
/* nav */
.nav{left:77px;top:154px;width:988px;height:70px;background:#fff;z-index:3}
.nav span{position:absolute;top:26px;font-size:14px;color:#475569}
.nav-phone{left:1065px;top:154px;width:73px;height:70px;background:#3a4f6b;z-index:3}
/* hero */
.hero{left:0;top:154px;width:1200px;height:796px;background:linear-gradient(120deg,#1e2a38 0%,#3c4d60 45%,#6b7783 80%,#8a8f95 100%)}
.hero-shade{left:0;top:154px;width:1200px;height:796px;background:linear-gradient(90deg,rgba(20,30,45,.75),rgba(20,30,45,.1))}
.tag{left:100px;top:451px;width:262px;height:41px;background:#3d5677;border-left:4px solid var(--blue);color:#fff;font-weight:700;font-size:19px;padding:9px 0 0 17px;font-family:"Rubik",sans-serif}
.hero h1{left:100px;top:515px;font-size:52px;color:#fff;font-weight:600}
.hero-p{left:100px;top:610px;width:480px;font-size:17px;line-height:26px;color:#fff}
/* intro */
.intro h2{left:83px;top:1096px;font-size:41px;line-height:53px;color:var(--ink)}
.intro-sub{left:83px;top:1226px;font-size:22px;color:var(--ink);font-family:"Rubik",sans-serif}
.body-text{font-size:12.5px;line-height:21px;color:var(--muted)}
/* services */
.services-bg{left:0;top:1559px;width:1200px;height:648px;background:var(--soft)}
.svc{width:318px;height:353px;top:1769px;border-radius:3px;overflow:hidden}
.svc h3{position:absolute;left:28px;top:226px;font-size:24px;color:#fff;font-weight:600}
.svc .dot{position:absolute;left:22px;top:232px;width:20px;height:20px;border-radius:50%;background:var(--blue)}
.svc .go{position:absolute;left:27px;top:277px;width:50px;height:50px;border-radius:50%;background:rgba(255,255,255,.22);display:flex;align-items:center;justify-content:center}
/* experts */
.experts-bg{left:0;top:2207px;width:1200px;height:387px;background:linear-gradient(100deg,#22344f,#34496a 60%,#3b5070)}
.xcard{top:2321px;width:235px;height:365px;background:#fff;box-shadow:0 4px 18px rgba(20,40,70,.14);text-align:center}
.xcard svg{margin-top:30px}
.xcard h3{font-size:21px;font-weight:400;color:var(--ink);margin-top:12px}
.xcard p{font-size:12.5px;line-height:19px;color:var(--muted);padding:20px 24px 0}
.xcard a{display:block;margin-top:28px;font-size:13px;font-weight:700;color:var(--ink);text-decoration:none}
/* why */
.why-title{font-size:30px;color:var(--ink)}
.why-item h3{font-size:20px;font-weight:400;color:var(--ink)}
.why-item p{font-size:12.5px;line-height:18px;color:var(--muted)}
.why-icon{width:80px;height:80px;border-radius:50%;background:#fff;box-shadow:0 4px 16px rgba(20,40,70,.13);display:flex;align-items:center;justify-content:center}
/* testimonials */
.testi-bg{left:0;top:3333px;width:1200px;height:536px;background:var(--navy-deep)}
.tcard{top:3547px;width:321px;height:217px;background:var(--navy-card);border-radius:3px;color:#fff}
.tcard .q{position:absolute;left:141px;top:-6px;font-size:60px;font-family:"Rubik",sans-serif;color:var(--blue);font-weight:600}
.tcard p{position:absolute;left:32px;top:32px;width:262px;font-size:13px;line-height:20px}
.tcard .av{position:absolute;left:28px;top:140px;width:48px;height:48px;border-radius:50%;background:linear-gradient(#e3cdbb,#b99883);border:3px solid #fff}
.tcard b{position:absolute;left:92px;top:142px;font-size:15px;font-weight:400}
.tcard em{position:absolute;left:92px;top:164px;font-size:15px;font-style:normal;color:#8497ae}
/* contact */
.info-item b{display:block;font-size:12px;font-weight:600;color:var(--ink)}
.info-item span{font-size:12px;color:var(--muted)}
.form-card{left:597px;top:3977px;width:494px;height:568px;background:#fff;border-top:5px solid var(--navy);box-shadow:0 6px 30px rgba(20,40,70,.15);z-index:4}
.form-card label{position:absolute;font-size:13px;font-weight:600;color:var(--ink)}
.field{position:absolute;border:1px solid #c9d2dc;border-radius:22px;font-size:12px;color:#8b95a1;padding:12px 0 0 22px}
.footer-bg{left:0;top:4340px;width:1200px;height:501px;background:var(--navy)}
.f-info{font-size:13px;line-height:19px;color:#fff;display:flex;gap:12px;align-items:center}
.fnav span{position:absolute;top:18px;font-size:14px;color:#fff}
</style>
</head>
<body>

<!-- top bar -->
<div class="abs topbar">
  <span style="left:78px">◷ &nbsp;Mon-Sat: 09am to 07:30pm</span>
  <span style="left:326px">✉ &nbsp;info@company.com</span>
  <span style="left:868px;top:12px;height:22px;border-left:1px solid #6c7d95"></span>
  <span style="left:886px">Faqs</span>
  <span style="left:936px;top:12px;height:22px;border-left:1px solid #6c7d95"></span>
  <span style="left:954px">Pricing</span>
</div>

<!-- header -->
<div class="abs logo" style="left:88px;top:76px;font-size:34px"><i style="width:30px;height:30px"></i>Zvo Klinieken</div>
<svg class="abs" style="left:364px;top:82px" width="34" height="34" viewBox="0 0 34 34" fill="none" stroke="#27374f" stroke-width="2"><path d="M17 4a13 12 0 1 1-8 22l-5 3 2-6A13 12 0 0 1 17 4z"/><circle cx="11" cy="16" r="1.2" fill="#27374f"/><circle cx="17" cy="16" r="1.2" fill="#27374f"/><circle cx="23" cy="16" r="1.2" fill="#27374f"/></svg>
<div class="abs contact-item" style="left:413px;top:76px">+12-345-67-8900<br><small>Needhelp? Make a Call</small></div>
<svg class="abs" style="left:664px;top:82px" width="34" height="34" viewBox="0 0 34 34" fill="none" stroke="#27374f" stroke-width="2"><circle cx="17" cy="17" r="14"/><ellipse cx="17" cy="17" rx="6" ry="14"/><path d="M3 17h28M5 10h24M5 24h24"/></svg>
<div class="abs contact-item" style="left:712px;top:76px">City, Country<br><small>123A Someplace</small></div>
<div class="btn" style="left:958px;top:75px;width:180px;height:49px;font-size:13px">Free Estimate <svg width="20" height="20" viewBox="0 0 20 20" fill="none" stroke="#fff" stroke-width="2"><circle cx="10" cy="10" r="8"/><path d="M9 6l4 4-4 4"/></svg></div>

<!-- hero -->
<div class="abs hero" role="img" aria-label="Foto: tandarts met mondkapje behandelt een oudere patiënt"></div>
<div class="abs hero-shade"></div>
<div class="abs nav">
  <span style="left:109px">THUIS</span><span style="left:181px">Behandelingen</span><span style="left:349px">Vergoeding</span><span style="left:474px">Ons team</span><span style="left:586px">Folders</span><span style="left:692px">Gallery</span><span style="left:799px">Contact Us</span>
</div>
<div class="abs nav-phone"><svg style="margin:18px 0 0 19px" width="36" height="34" viewBox="0 0 36 34" fill="none" stroke="#fff" stroke-width="2"><path d="M8 3l6 7-4 4c2 5 6 9 11 11l4-4 7 6-4 5C16 31 4 19 3 7z"/></svg></div>
<div class="abs tag">Kaakchirurgie</div>
<h1 class="abs hero">Precisiechirurgie</h1>
<p class="abs hero-p">Lorem ipsum dolor sit amet, consectetur adipiscing elit, sed do eiusmod tempor incididunt ut labore et d</p>
<div class="btn" style="left:100px;top:689px;width:176px;height:51px">Meer Leren</div>
<svg class="abs" style="left:0;top:810px" width="1200" height="150" viewBox="0 0 1200 150" preserveAspectRatio="none">
  <path d="M0 125 C400 100 800 60 1200 8 L1200 150 L0 150Z" fill="#fff"/>
  <path d="M0 110 C250 126 500 110 700 84 C480 116 240 140 0 142Z" fill="#1b9ee0"/>
</svg>

<!-- intro -->
<div class="kicker" style="left:83px;top:1063px">Kwaliteitsborging</div>
<h2 class="abs intro" style="left:83px;top:1096px;font-size:41px;line-height:53px">Harmonie in Vorm,<br>Precisie in Functie</h2>
<div class="abs intro-sub">Zelfvertrouwen Boetseren, Levens Vormgeven</div>
<p class="abs body-text" style="left:83px;top:1273px;width:502px">Lorem ipsum dolor sit amet, consectetur adipiscing elit, sed do eiusmod tempor incididunt ut labore et dolore magna aliqua. Ut enim ad minim veniam, quis nos trud exercitation ullamco laboris nisi ut aliquip ex ea commodo consequat. Duis aute irure dolor in reprehenderit in voluptate velit esse cillum dolore eu fugiat nulla pariatur. Excepteur sint occaecat cupidatat non proident, sunt in culpa qui officia deserunt mollit anim id est laborum.</p>
<div class="btn" style="left:83px;top:1431px;width:154px;height:45px">Meer Leren <span>→</span></div>
<div class="photo" style="left:618px;top:1046px;width:236px;height:426px;background:linear-gradient(160deg,#d8e6ef,#a9c1d3 55%,#e5b98f)" role="img" aria-label="Foto: lachend meisje met een tandheelkundig model"></div>
<div class="photo" style="left:870px;top:1078px;width:238px;height:424px;background:linear-gradient(160deg,#c5d0d8,#7d93a6 50%,#b38b74)" role="img" aria-label="Foto: glimlachende vrouw bekijkt haar tanden in een spiegel"></div>
<div class="abs" style="left:820px;top:1237px;width:76px;height:76px;border-radius:50%;background:#3a4f6b;border:4px solid #fff;display:flex;align-items:center;justify-content:center"><svg width="34" height="34" viewBox="0 0 34 34" fill="none" stroke="#fff" stroke-width="2"><path d="M9 5c4 0 5 2 8 2s4-2 8-2c4 0 6 4 5 9-1 4-2 6-3 12-1 4-4 4-5 0l-2-6c-1-2-5-2-6 0l-2 6c-1 4-4 4-5 0-1-6-2-8-3-12C3 9 5 5 9 5z"/></svg></div>

<!-- services -->
<div class="abs services-bg"></div>
<div class="kicker" style="left:86px;top:1619px;text-transform:none">Onze Diensten</div>
<h2 class="abs" style="left:88px;top:1654px;font-size:41px;color:var(--ink)">Onze Diensten</h2>
<div class="abs" style="left:943px;top:1670px;font-size:14px;color:var(--ink)">More Services</div>
<div class="abs" style="left:1076px;top:1660px;width:39px;height:38px;background:var(--blue);color:#fff;font-size:20px;text-align:center;line-height:36px">›</div>
<div class="abs svc" style="left:96px;background:linear-gradient(#9fb9cf,#35506f 75%,#1f3656)" role="img" aria-label="Foto: vrouw in de behandelstoel bij de kaakchirurg"><span class="dot"></span><h3>Kaakchirurgie</h3><span class="go"><svg width="18" height="18" viewBox="0 0 18 18" fill="none" stroke="#fff" stroke-width="2"><path d="M3 9h12M10 4l5 5-5 5"/></svg></span></div>
<div class="abs svc" style="left:443px;background:linear-gradient(#a6b8c7,#3b5574 75%,#1f3656)" role="img" aria-label="Foto: glimlachende vrouwelijke patiënt"><span class="dot"></span><h3>Slaapgeneeskunde</h3><span class="go"><svg width="18" height="18" viewBox="0 0 18 18" fill="none" stroke="#fff" stroke-width="2"><path d="M3 9h12M10 4l5 5-5 5"/></svg></span></div>
<div class="abs svc" style="left:789px;background:linear-gradient(#b4c6d6,#3e5877 75%,#1f3656)" role="img" aria-label="Foto: lachend jong meisje bij de tandarts"><span class="dot"></span><h3>Plastische Chirurgie</h3><span class="go"><svg width="18" height="18" viewBox="0 0 18 18" fill="none" stroke="#fff" stroke-width="2"><path d="M3 9h12M10 4l5 5-5 5"/></svg></span></div>

<!-- experts -->
<div class="abs experts-bg" role="img" aria-label="Achtergrondfoto: tandartsteam aan het werk, donker getint"></div>
<h2 class="abs" style="left:88px;top:2316px;font-size:40px;line-height:53px;color:#fff;font-weight:600">Leading<br>Experts</h2>
<div class="btn" style="left:88px;top:2481px;width:156px;height:45px;font-size:14px">Contact us <span>→</span></div>
<div class="abs xcard" style="left:353px"><svg width="48" height="56" viewBox="0 0 48 56" fill="none" stroke="#1b9ee0" stroke-width="2.5"><path d="M18 30V8a4 4 0 0 1 8 0v16l10 3c4 1 5 4 4 8l-3 12H20l-9-11c-2-3 1-6 4-4l3 3"/></svg><h3>Professioneel</h3><p>Lorem ipsum dolor sit amet, consectetur adipiscing elit, sed do eiusmod tem por incididunt ut labore et dolore magna aliqua. Ut enim ad minim veniam.</p><a>Read More →</a></div>
<div class="abs xcard" style="left:612px"><svg width="52" height="56" viewBox="0 0 52 56" fill="none" stroke="#1b9ee0" stroke-width="2.5"><circle cx="37" cy="10" r="5"/><path d="M31 52V22h12v30M4 52V38h8v14M17 52V28h8v24M4 30l16-14 6 5"/></svg><h3>Ervaring</h3><p>Lorem ipsum dolor sit amet, consectetur adipiscing elit, sed do eiusmod tem por incididunt ut labore et dolore magna aliqua. Ut enim ad minim veniam.</p><a>Read More →</a></div>
<div class="abs xcard" style="left:875px"><svg width="48" height="56" viewBox="0 0 48 56" fill="none" stroke="#1b9ee0" stroke-width="2.5"><circle cx="24" cy="18" r="9"/><path d="M6 48c0-10 8-16 18-16s18 6 18 16H6z"/></svg><h3>Expertise</h3><p>Lorem ipsum dolor sit amet, consectetur adipiscing elit, sed do eiusmod tem por incididunt ut labore et dolore magna aliqua. Ut enim ad minim veniam.</p><a>Read More →</a></div>

<!-- why -->
<div class="kicker" style="left:574px;top:2739px">Why Us</div>
<h2 class="abs why-title" style="left:0;top:2776px;width:1212px;text-align:center;font-size:41px">Waarom Ons Kiezen</h2>
<div class="abs" style="left:432px;top:2865px;width:330px;height:370px;border-radius:0 0 165px 165px;overflow:hidden">
  <div style="position:absolute;left:0;top:40px;width:330px;height:330px;border-radius:50%;background:linear-gradient(#1e3f78,#2b4f8a)"></div>
  <div style="position:absolute;left:65px;top:0;width:200px;height:370px;border-radius:100px 100px 0 0;background:linear-gradient(#c9a88f 0%,#c9a88f 28%,#6c727c 30%,#5b616b)" role="img" aria-label="Foto: glimlachende arts in grijs pak met gekruiste armen"></div>
</div>
<div class="abs why-item" style="left:100px;top:2912px;width:223px;text-align:right"><h3>Kwaliteitsborging</h3><p>Lorem ipsum dolor sit amet, consectetur adipiscing elit</p></div>
<div class="abs why-item" style="left:62px;top:3038px;width:223px;text-align:right"><h3>Ervaring</h3><p>Lorem ipsum dolor sit amet, consectetur adipiscing elit</p></div>
<div class="abs why-item" style="left:96px;top:3162px;width:223px;text-align:right"><h3>Persoonlijke Aanpak</h3><p>Lorem ipsum dolor sit amet, consectetur adipiscing elit</p></div>
<div class="abs why-item" style="left:892px;top:2912px;width:230px"><h3>Klantgericht</h3><p>Lorem ipsum dolor sit amet, consectetur adipiscing elit</p></div>
<div class="abs why-item" style="left:901px;top:3038px;width:230px"><h3>Professioneel</h3><p>Lorem ipsum dolor sit amet, consectetur adipiscing elit</p></div>
<div class="abs why-item" style="left:877px;top:3162px;width:240px"><h3>Bewezen Track Record</h3><p>Lorem ipsum dolor sit amet, consectetur adipiscing elit</p></div>
<div class="abs why-icon" style="left:354px;top:2905px"><svg width="30" height="30" viewBox="0 0 30 30" fill="none" stroke="#1b9ee0" stroke-width="2"><circle cx="15" cy="5" r="3"/><path d="M4 11h22M15 11v8l-6 9M15 19l6 9"/></svg></div>
<div class="abs why-icon" style="left:319px;top:3031px"><svg width="30" height="30" viewBox="0 0 30 30" fill="none" stroke="#1b9ee0" stroke-width="2.5" stroke-dasharray="3 4"><circle cx="15" cy="15" r="11"/></svg></div>
<div class="abs why-icon" style="left:352px;top:3155px"><svg width="30" height="30" viewBox="0 0 30 30" fill="none" stroke="#1b9ee0" stroke-width="2"><path d="M5 18a10 10 0 0 1 20 0v4H5zM9 22v4h12v-4"/></svg></div>
<div class="abs why-icon" style="left:762px;top:2905px"><svg width="30" height="30" viewBox="0 0 30 30" fill="none" stroke="#1b9ee0" stroke-width="2"><circle cx="15" cy="15" r="11"/><circle cx="15" cy="15" r="6"/><circle cx="15" cy="15" r="2" fill="#1b9ee0"/></svg></div>
<div class="abs why-icon" style="left:796px;top:3031px"><svg width="30" height="30" viewBox="0 0 30 30" fill="none" stroke="#1b9ee0" stroke-width="2"><path d="M5 18a10 10 0 0 1 20 0v4H5zM9 22v4h12v-4"/></svg></div>
<div class="abs why-icon" style="left:762px;top:3155px"><svg width="30" height="30" viewBox="0 0 30 30" fill="none" stroke="#1b9ee0" stroke-width="2"><rect x="3" y="3" width="7" height="7"/><rect x="20" y="3" width="7" height="7"/><rect x="3" y="20" width="7" height="7"/><rect x="20" y="20" width="7" height="7"/><path d="M10 6h10M6 10v10M24 10v10M10 24h10"/></svg></div>

<!-- testimonials -->
<div class="abs testi-bg"></div>
<div class="kicker" style="left:546px;top:3388px;color:var(--blue);text-decoration:none">Getuigenissen</div>
<h2 class="abs" style="left:0;top:3424px;width:1212px;text-align:center;font-size:41px;color:#fff">Wat Klanten Zeggen</h2>
<div class="abs tcard" style="left:94px"><span class="q">❞❞</span><p>Lorem ipsum dolor sit amet, consectetur adipiscing elit, sed do eiusmod tem por incididunt ut labore et dolore magna aliqua. Ut enim ad minim veniam, q uis nostrud exercitation ullamco laboris</p><span class="av"></span><b>Lotte D.</b><em>Brussels</em></div>
<div class="abs tcard" style="left:441px"><span class="q">❞❞</span><p>Lorem ipsum dolor sit amet, consectetur adipiscing elit, sed do eiusmod tem por incididunt ut labore et dolore magna aliqua. Ut enim ad minim veniam, q uis nostrud exercitation ullamco laboris</p><span class="av"></span><b>Lotte D.</b><em>Brussels</em></div>
<div class="abs tcard" style="left:787px"><span class="q">❞❞</span><p>Lorem ipsum dolor sit amet, consectetur adipiscing elit, sed do eiusmod tem por incididunt ut labore et dolore magna aliqua. Ut enim ad minim veniam, q uis nostrud exercitation ullamco laboris</p><span class="av"></span><b>Lotte D.</b><em>Brussels</em></div>
<svg class="abs" style="left:566px;top:3787px" width="70" height="12"><circle cx="4" cy="6" r="3" fill="#8aa3c0"/><circle cx="19" cy="6" r="3" fill="#8aa3c0"/><circle cx="34" cy="6" r="4" fill="#e05a4a"/><circle cx="49" cy="6" r="3" fill="#8aa3c0"/><circle cx="64" cy="6" r="3" fill="#8aa3c0"/></svg>

<!-- contact -->
<h2 class="abs" style="left:101px;top:3977px;font-size:39px;color:var(--ink)">Kom Met Ons In Contact</h2>
<svg class="abs" style="left:118px;top:4062px" width="38" height="38" viewBox="0 0 38 38" fill="none" stroke="#7badd7" stroke-width="2"><circle cx="19" cy="13" r="6"/><path d="M19 32S9 22 9 13a10 10 0 0 1 20 0c0 9-10 19-10 19zM4 34h30"/></svg>
<div class="abs info-item" style="left:182px;top:4057px"><b>HEAD OFFICE</b><span>21 Lorem Ipsum, ABC 123</span></div>
<svg class="abs" style="left:118px;top:4132px" width="38" height="34" viewBox="0 0 38 34" fill="none" stroke="#7badd7" stroke-width="2"><rect x="4" y="6" width="30" height="22"/><path d="M4 6l15 12 15-12"/></svg>
<div class="abs info-item" style="left:182px;top:4129px"><b>EMAIL ADDRESS</b><span>21 Lorem Ipsum, ABC 123</span></div>
<svg class="abs" style="left:118px;top:4197px" width="38" height="38" viewBox="0 0 38 38" fill="none" stroke="#7badd7" stroke-width="2"><rect x="10" y="4" width="18" height="30" rx="3"/><path d="M17 29h4M31 14c2 2 2 8 0 10"/></svg>
<div class="abs info-item" style="left:182px;top:4194px"><b>CALL US NOW</b><span>21 Lorem Ipsum, ABC 123</span></div>

<div class="abs footer-bg"></div>
<svg class="abs" style="left:0;top:4320px" width="1200" height="140" viewBox="0 0 1200 140" preserveAspectRatio="none">
  <path d="M0 0H1200V65C800 60 300 90 0 130Z" fill="#fff"/>
  <path d="M500 78C640 70 720 64 780 60C700 70 600 78 500 84Z" fill="#1b9ee0"/>
  <path d="M1060 25C1110 23 1160 22 1200 22V40C1150 38 1100 32 1060 25Z" fill="#1b9ee0"/>
</svg>

<div class="abs form-card">
  <div style="position:absolute;left:36px;top:52px;font-size:23px;font-family:Rubik,sans-serif;font-weight:500;color:var(--ink)">Send Us A Message</div>
  <label style="left:38px;top:113px">First Name</label><label style="left:250px;top:113px">Last Name</label>
  <div class="field" style="left:38px;top:130px;width:199px;height:42px">John</div>
  <div class="field" style="left:250px;top:130px;width:197px;height:42px">Doe</div>
  <label style="left:38px;top:199px">Email</label>
  <div class="field" style="left:38px;top:217px;width:415px;height:41px">info@company.com</div>
  <label style="left:38px;top:289px">Message</label>
  <div class="field" style="left:38px;top:307px;width:415px;height:122px;border-radius:14px">Type Your Message</div>
  <div class="btn" style="left:38px;top:469px;width:156px;height:45px;font-size:14px">Contact us <span>→</span></div>
</div>

<!-- footer -->
<div class="abs logo" style="left:152px;top:4582px;font-size:40px;color:#5aaee8"><i style="width:34px;height:34px;border-color:#5aaee8"></i>Zvo Klinieken</div>
<div class="abs" style="left:411px;top:4612px;height:40px;border-left:1px solid #55698a"></div>
<div class="abs f-info" style="left:432px;top:4614px"><svg width="28" height="28" viewBox="0 0 28 28" fill="none" stroke="#fff" stroke-width="1.8"><circle cx="14" cy="14" r="12"/><ellipse cx="14" cy="14" rx="5" ry="12"/><path d="M2 14h24"/></svg><span>123, Building Name, Street<br>City, State XY 123456</span></div>
<div class="abs" style="left:670px;top:4612px;height:40px;border-left:1px solid #55698a"></div>
<div class="abs f-info" style="left:689px;top:4614px"><svg width="28" height="30" viewBox="0 0 28 30" fill="none" stroke="#fff" stroke-width="1.8"><rect x="6" y="3" width="14" height="24" rx="2"/><path d="M23 11c2 2 2 6 0 8"/></svg><span>PHONE<br>(123) 456 7890</span></div>
<div class="abs" style="left:849px;top:4612px;height:40px;border-left:1px solid #55698a"></div>
<div class="abs f-info" style="left:866px;top:4614px"><svg width="30" height="26" viewBox="0 0 30 26" fill="none" stroke="#fff" stroke-width="1.8"><rect x="3" y="4" width="24" height="18"/><path d="M3 4l12 10 12-10"/></svg><span>EMAIL<br>info@company.com</span></div>
<div class="abs fnav" style="left:257px;top:4698px;width:720px;height:52px;border-top:1px solid #55698a;border-bottom:1px solid #55698a">
  <span style="left:18px">HOME</span><span style="left:112px">SERVICES</span><span style="left:219px">ABOUT US</span><span style="left:337px">TESTIMONIALS</span><span style="left:490px">BLOG</span><span style="left:582px">CONTACT US</span>
</div>
<div class="abs" style="left:147px;top:4790px;font-size:11px;color:#fff">Zvo Klinieken</div>

</body>
</html>
```